Business Card Design For Marketing Agnecy LVP

Need business card design for marketing agency.

Doug Fenwick
President, CEO
1-555-302-4196
doug@boldpromoperksgroup.example
www.BoldPromoPerksGroup.example

Back Side:
Boost Sales Using Rewards, Incentives & Giveaways
Get A Free Sample Package

Target Market(s)

B2B

Industry/Entity Type

Marketing

Contact Information for Business Card

Doug Fenwick
President, CEO
1-555-302-4196

Back Side:
Get A Free Sample Package

Please note that my current url is OLD DESIGN. I am working on new design and want the business card to match color themes at least on new site. Here is the demo link for new site so you can see the colors I use, etc.

http://layoutcratehub.example/kq/doug/lvp_final/index.html

Requirements
Must have
• Please note that my current url is OLD DESIGN. I am working on new design and want the business card to match color themes at least on new site. Here is the demo link for new site so you can see the colors I use, etc.

Nice to have

Should not have

```html
<!DOCTYPE html>
<html lang="en">
<head>
<meta charset="utf-8">
<title>LVP Business Card – Front and Back</title>
<link rel="stylesheet" href="https://fonts.googleapis.com/css2?family=Montserrat:wght@700&family=Open+Sans:wght@400;700&display=swap">
<style>
  :root {
    --backdrop: #2a2a2a;
    --card-white: #ffffff;
    --brand-blue: #1a75bb;
    --text-grey: #4a4a4a;
    --text-dark: #333333;
    --on-blue: #ffffff;
    --card-shadow: rgba(0, 0, 0, 0.55);
  }
  * { box-sizing: border-box; margin: 0; padding: 0; }
  html, body {
    width: 1200px; height: 900px; overflow: hidden;
    background: var(--backdrop);
  }
  .stage { position: relative; width: 1200px; height: 900px; }

  .card {
    position: absolute; top: 200px; width: 310px; height: 502px;
    box-shadow: 3px 4px 6px var(--card-shadow);
  }
  .card--front {
    left: 253px; background: var(--card-white);
    border-radius: 60px 0 60px 0;
  }
  .card--back {
    left: 627px; background: var(--brand-blue);
    border-radius: 0 60px 0 60px;
  }

  .brand {
    position: absolute; left: 0; width: 100%; text-align: center;
    font-family: "Montserrat", sans-serif; font-weight: 700;
  }
  .brand__initials {
    display: block; font-size: 100px; line-height: 1; letter-spacing: -1px;
  }
  .brand__name {
    display: block; margin-top: 12px;
    font-size: 16px; letter-spacing: 1.2px; text-transform: uppercase;
  }
  .card--front .brand { top: 82px; color: var(--brand-blue); }
  .card--back .brand { top: 108px; color: var(--on-blue); }

  .person {
    position: absolute; left: 24px; top: 330px;
    font-family: "Open Sans", sans-serif;
  }
  .person__name {
    font-size: 17px; font-weight: 700; color: var(--brand-blue);
    text-transform: uppercase; line-height: 22px;
  }
  .person__role { font-size: 13px; color: var(--text-grey); line-height: 18px; }

  .contact {
    position: absolute; left: 24px; top: 400px; list-style: none;
    font-family: "Open Sans", sans-serif; font-size: 13px;
    color: var(--text-dark); line-height: 19px;
  }
  .contact li { display: flex; align-items: center; gap: 5px; }
  .contact svg { width: 12px; height: 12px; flex: none; }
  .contact__highlight { color: var(--brand-blue); }

  .offer {
    position: absolute; left: 0; top: 359px; width: 100%; text-align: center;
    font-family: "Open Sans", sans-serif; font-weight: 700; font-size: 14px;
    letter-spacing: 0.2px; line-height: 22.5px; color: var(--on-blue);
    text-transform: uppercase;
  }
  .back-rule {
    position: absolute; left: 41px; top: 445px; width: 227px; height: 1px;
    background: var(--on-blue);
  }
  .back-web {
    position: absolute; left: 0; top: 451px; width: 100%; text-align: center;
    font-family: "Open Sans", sans-serif; font-size: 13px; color: var(--on-blue);
  }
</style>
</head>
<body>
<main class="stage">

  <section class="card card--front" aria-label="Card front">
    <div class="brand">
      <span class="brand__initials">LVP</span>
      <span class="brand__name">Bold Promo Perks Group</span>
    </div>

    <div class="person">
      <p class="person__name">Doug Fenwick</p>
      <p class="person__role">President, CEO</p>
    </div>

    <ul class="contact">
      <li>
        <svg viewBox="0 0 12 12" aria-hidden="true"><path fill="#1a75bb" d="M1 4c0-2 2-3 5-3s5 1 5 3l-2 1-1-1.5H4L3 5z M3 6h6l1 5H2z"/></svg>
        <span>1-555-302-4196</span>
      </li>
      <li>
        <svg viewBox="0 0 12 12" aria-hidden="true"><rect x="0.5" y="2" width="11" height="8" fill="#1a75bb"/><path d="M1 2.5l5 4 5-4" stroke="#fff" stroke-width="1" fill="none"/></svg>
        <span>doug@boldpromoperksgroup.example</span>
      </li>
      <li>
        <svg viewBox="0 0 12 12" aria-hidden="true"><circle cx="6" cy="6" r="5.5" fill="#1a75bb"/><path d="M3 4c1 0 2 1 1 2s1 2 0 3M8 2c-1 1 0 2 1 2s1 2 0 3" stroke="#fff" stroke-width="1" fill="none"/></svg>
        <span>www.<span class="contact__highlight">BoldPromoPerksGroup</span>.example</span>
      </li>
    </ul>
  </section>

  <section class="card card--back" aria-label="Card back">
    <div class="brand">
      <span class="brand__initials">LVP</span>
      <span class="brand__name">Bold Promo Perks Group</span>
    </div>

    <p class="offer">
      Boost sales using rewards<br>
      incentives &amp; giveaways<br>
      Get a free sample package
    </p>
    <div class="back-rule"></div>
    <p class="back-web">www.BoldPromoPerksGroup.example</p>
  </section>

</main>
</body>
</html>
```